Local fast-growing company in the service sector

We are looking for a modern business card design, which should also appear on our letterheads

Target Market(s)

Private and industrial sectors

Contact Information for Business Card

Vorname Name
Kellberger Str. 18
72816 Lindenau
Tel.: 07146-839214-0
Name@agentur-kvtl.de

Colors
9d9d9d
919191
aaaaaa

Requirements
Must have
• The logo (file) in silver

```html
<!DOCTYPE html>
<html lang="de">
<head>
<meta charset="utf-8">
<title>KVTL Visitenkarte</title>
<link href="https://fonts.googleapis.com/css2?family=Lato:wght@400;700&display=swap" rel="stylesheet">
<style>
  :root {
    --page-bg: #e9e7e4;
    --card-top: #f3f3f2;
    --card-bottom: #dcdcdb;
    --card-edge: #aaaaaa;
    --ink: #3d3d3f;
    --ink-soft: #4a4a4c;
    --silver: #9d9d9d;
    --silver-dark: #6f6f72;
    --icon-bg: #919191;
  }
  html, body {
    margin: 0;
    padding: 0;
    width: 1200px;
    height: 970px;
    overflow: hidden;
    background: var(--page-bg);
    font-family: "Lato", sans-serif;
  }
  .business-card {
    position: absolute;
    left: 100px;
    top: 186px;
    width: 1000px;
    height: 597px;
    box-sizing: border-box;
    border: 1px solid var(--card-edge);
    background: linear-gradient(160deg, var(--card-top), var(--card-bottom));
    box-shadow: 0 18px 40px rgba(0,0,0,0.12);
  }
  .brand {
    position: absolute;
    left: 584px;
    top: 62px;
    display: flex;
    align-items: center;
    gap: 22px;
  }
  .brand-mark {
    width: 78px;
    height: 78px;
    border-radius: 50%;
    background: var(--silver);
  }
  .brand-name {
    font-weight: 700;
    font-size: 92px;
    line-height: 1;
    letter-spacing: 2px;
    color: var(--silver-dark);
  }
  .contact-block {
    position: absolute;
    left: 54px;
    top: 312px;
    color: var(--ink);
  }
  .person-name {
    margin: 0;
    font-weight: 700;
    font-size: 28px;
    line-height: 1.2;
  }
  .person-company {
    margin: 6px 0 0;
    font-size: 20px;
    color: var(--ink-soft);
  }
  .contact-list {
    list-style: none;
    margin: 36px 0 0;
    padding: 0;
  }
  .contact-item {
    display: flex;
    align-items: center;
    gap: 14px;
    font-size: 23px;
    height: 34px;
    margin-bottom: 14px;
  }
  .contact-icon {
    width: 32px;
    height: 32px;
    flex: none;
  }
  .address {
    margin: 6px 0 0;
    font-weight: 700;
    font-size: 21px;
  }
</style>
</head>
<body>
  <div class="business-card">
    <div class="brand">
      <span class="brand-mark"></span>
      <span class="brand-name">KVTL</span>
    </div>

    <div class="contact-block">
      <h1 class="person-name">Helena Brandt</h1>
      <p class="person-company">Norvik Partners</p>

      <ul class="contact-list">
        <li class="contact-item">
          <svg class="contact-icon" viewBox="0 0 32 32" aria-hidden="true">
            <circle cx="16" cy="16" r="16" fill="var(--icon-bg)"/>
            <path d="M9 12c0-2 2-3.5 7-3.5s7 1.5 7 3.5v1.5h-3.5v-2h-7v2H9z" fill="#f2f2f2"/>
            <rect x="10.5" y="15" width="11" height="8" rx="1.5" fill="#f2f2f2"/>
            <circle cx="16" cy="19" r="2" fill="var(--icon-bg)"/>
          </svg>
          <span>07146-839214-0</span>
        </li>
        <li class="contact-item">
          <svg class="contact-icon" viewBox="0 0 32 32" aria-hidden="true">
            <circle cx="16" cy="16" r="16" fill="var(--icon-bg)"/>
            <rect x="8.5" y="10.5" width="15" height="11" rx="1" fill="#f2f2f2"/>
            <path d="M8.5 11l7.5 6 7.5-6" fill="none" stroke="var(--icon-bg)" stroke-width="1.6"/>
          </svg>
          <span>Name@agentur-kvtl.de</span>
        </li>
      </ul>

      <p class="address">Kellberger Str. 18 72816 Lindenau</p>
    </div>
  </div>
</body>
</html>
```